job report

Designer – Professional Plumbing Job Report Template

Overview

We are seeking a skilled designer to create a professional, easy-to-use Job Report template for a commercial and maintenance plumbing business.
The report will be used for clients, property managers, facilities managers, strata, and retail centres and must clearly communicate findings, works completed, and recommendations in a polished, compliant, and branded format.

The final document must be suitable for PDF delivery, email, and ongoing reuse.

Objectives

Present plumbing works in a clear, professional, and defensible report format

Improve client understanding of findings and recommendations

Provide a repeatable template that can be used across maintenance, reactive, and investigative works

Allow easy insertion of text, tables, and photos

Report Structure (Minimum Inclusions)
1. Cover Page

Company logo and branding

Report title (e.g. Plumbing Job Report / Investigation Report)

Client name

Site address

Job reference / work order number

Date of attendance

Technician / contractor name

2. Client & Site Details

Client / company name

Site address

Contact person

Contact details

Access notes (after-hours, tenant access, etc.)

3. Reason for Attendance

Clear description of why attendance was required

Call-out type (reactive, scheduled maintenance, investigation, emergency, etc.)

Reported issue or scope requested by client

4. Findings / Observations

Detailed findings discovered on site

Condition of pipework, fixtures, drainage, or systems

Any contributing factors identified

Notes on compliance, wear, damage, or risk

(This section should support bullet points and paragraphs.)

5. Works Carried Out

Step-by-step description of works completed

Equipment used (e.g. jetter, CCTV camera, leak detection, flex shaft, etc.)

Repairs, replacements, testing, and verification

Confirmation that systems were tested and operational on completion

6. Photos & Visual Evidence

Clearly labelled photo sections

Before / during / after photos

Space for photo captions and explanations

Logical layout that aligns photos with written findings

7. Recommendations

Clearly separated from works completed

Urgent vs non-urgent recommendations

Preventative maintenance advice

Upgrade or replacement suggestions

Risk-based language where appropriate

8. Limitations & Exclusions

Areas not inspected

Access limitations

Assumptions made during inspection

Items outside scope of works

9. Conclusion

Summary of outcome

Confirmation of current system status

Next steps (if any)

10. Sign-Off

Contractor / technician name

Company name

Date

Optional client acknowledgement section

Design Requirements

Clean, professional layout

Commercial / trade-appropriate styling (not overly creative)

Easy-to-read fonts

Consistent headings and spacing

Logical flow for busy property managers

Editable format (Word / Google Docs / InDesign source file)

Final export-ready PDF version

Bonus (Nice to Have)

Traffic-light system (Green / Amber / Red) for condition reporting

Iconography for findings, repairs, and recommendations

Optional sections for compliance notes (AS/NCC references)

Space for QR codes or job reference numbers

Deliverables

Editable master report template

PDF version

Instructions or notes for ongoing use

```html
<!DOCTYPE html>
<html lang="en">
<head>
<meta charset="utf-8">
<title>Tideline Plumbing – Job Report Template</title>
<link href="https://fonts.googleapis.com/css2?family=Orbitron:wght@600;700&family=Roboto:wght@400;500;900&display=swap" rel="stylesheet">
<style>
  :root{
    --backdrop:#8d8b88;
    --paper:#ffffff;
    --brand-blue:#2ab6de;
    --brand-yellow:#f5be3f;
    --ink:#2b2b2b;
    --ink-soft:#444;
    --field-border:#d9dde0;
    --rule:#e3f1f6;
    --wave-light:#86d6e6;
    --wave-mid:#4dbbd6;
    --wave-deep:#2fa3c4;
    --wave-pale:#a9e2ee;
  }
  *{box-sizing:border-box;margin:0;padding:0}
  html,body{width:1200px;height:3849px;overflow:hidden}
  body{background:var(--backdrop);font-family:"Roboto",sans-serif;color:var(--ink);position:relative}
  .page{position:absolute;left:193px;width:815px;height:1121px;background:var(--paper);overflow:hidden;box-shadow:0 6px 24px rgba(0,0,0,.25)}
  .page--cover{top:185px}
  .page--client{top:1364px}
  .page--reason{top:2543px}

  .brand{position:absolute;top:70px;left:0;width:100%;text-align:center}
  .brand__name{font-family:"Roboto",sans-serif;font-weight:900;font-size:64px;color:var(--brand-blue);letter-spacing:1px;line-height:1}
  .brand__sub{font-family:"Roboto",sans-serif;font-weight:900;font-size:40px;color:var(--brand-blue);letter-spacing:6px;margin-top:14px}
  .cover-rule{position:absolute;top:279px;left:0;width:100%;height:4px;background:var(--rule)}

  .label{position:absolute;font-size:17px;color:var(--ink);line-height:1.4}
  .field{position:absolute;border:2px solid var(--field-border);border-radius:7px;background:#fff;height:36px}
  .field--tall{height:78px}
  .checks{position:absolute;display:flex;gap:16px;font-size:14px;color:var(--ink-soft);align-items:center;flex-wrap:wrap;row-gap:10px}
  .check{display:flex;align-items:center;gap:8px}
  .check::before{content:"";width:12px;height:12px;border:1.6px solid #333;border-radius:2px}

  .section-band{position:absolute;top:46px;left:0;height:81px;background:var(--brand-yellow);border-radius:0 41px 41px 0;display:flex;align-items:center;padding-left:68px}
  .section-band__title{font-family:"Orbitron",sans-serif;font-weight:700;font-size:33px;color:#fff;letter-spacing:1px}

  .intro{position:absolute;left:57px;top:190px;width:700px;font-size:13.5px;line-height:1.9;color:var(--ink-soft)}

  .waves{position:absolute;left:0;bottom:0;width:815px}
  .photo{position:absolute;left:409px;top:751px;width:344px;height:344px;border-radius:50%;border:8px solid #fff;background:radial-gradient(circle at 55% 40%,#d7d9dc 0%,#9aa3ad 45%,#3c4656 100%)}
  .page-num{position:absolute;top:1079px;width:28px;height:28px;border-radius:50%;background:#fff;color:var(--brand-blue);font-size:11px;display:flex;align-items:center;justify-content:center}
</style>
</head>
<body>

<section class="page page--cover">
  <div class="brand">
    <div class="brand__name">TIDELINE</div>
    <div class="brand__sub">PLUMBING</div>
  </div>
  <div class="cover-rule"></div>

  <div class="label" style="left:67px;top:352px">Report title</div>
  <div class="checks" style="left:387px;top:347px"><span class="check">Plumbing Job Report</span><span class="check">Investigation Report)</span></div>
  <div class="label" style="left:67px;top:415px">Client name</div>
  <div class="field" style="left:387px;top:400px;width:360px"></div>
  <div class="label" style="left:67px;top:478px">Site address</div>
  <div class="field field--tall" style="left:387px;top:455px;width:360px"></div>
  <div class="label" style="left:67px;top:549px">Job reference / work order number</div>
  <div class="field" style="left:387px;top:551px;width:360px"></div>
  <div class="label" style="left:67px;top:603px">Date of attendance</div>
  <div class="field" style="left:387px;top:605px;width:360px"></div>
  <div class="label" style="left:67px;top:670px">Technician / contractor name</div>
  <div class="field" style="left:387px;top:661px;width:360px"></div>

  <svg class="waves" viewBox="0 0 815 380" height="380" aria-hidden="true">
    <path d="M0 10 C230 -10 420 40 815 300 L815 380 L0 380Z" fill="var(--wave-mid)"/>
    <path d="M0 40 C240 20 430 80 815 320" fill="none" stroke="#fff" stroke-width="9"/>
    <path d="M0 80 C250 60 450 120 815 350 L815 380 L0 380Z" fill="var(--wave-deep)"/>
    <path d="M0 180 C200 150 430 190 815 380 L0 380Z" fill="var(--wave-light)"/>
    <path d="M0 170 C220 135 440 180 815 370" fill="none" stroke="#fff" stroke-width="10"/>
  </svg>
  <div class="photo" role="img" aria-label="Photo of a plumber repairing pipework under a kitchen sink"></div>
</section>

<section class="page page--client">
  <div class="section-band" style="width:607px"><span class="section-band__title">CLIENT &amp; SITE DETAILS</span></div>

  <div class="label" style="left:70px;top:205px">Client / company name</div>
  <div class="field" style="left:336px;top:199px;width:408px"></div>
  <div class="label" style="left:70px;top:272px">Site address</div>
  <div class="field field--tall" style="left:336px;top:257px;width:408px"></div>
  <div class="label" style="left:70px;top:339px">Contact person</div>
  <div class="field" style="left:336px;top:355px;width:408px"></div>
  <div class="label" style="left:70px;top:406px">Contact details</div>
  <div class="field field--tall" style="left:336px;top:409px;width:408px"></div>
  <div class="label" style="left:70px;top:506px">Access notes</div>
  <div class="checks" style="left:336px;top:509px"><span class="check">After-Hours</span><span class="check">Tenant Access</span></div>

  <svg class="waves" viewBox="0 0 815 481" height="481" aria-hidden="true">
    <path d="M0 20 C260 0 470 70 815 360 L815 481 L0 481Z" fill="var(--wave-light)"/>
    <path d="M0 55 C270 35 480 110 815 390" fill="none" stroke="#fff" stroke-width="8"/>
    <path d="M0 110 C280 80 500 150 815 420 L815 481 L0 481Z" fill="var(--wave-mid)"/>
    <path d="M0 170 C280 140 500 200 815 440 L815 481 L0 481Z" fill="var(--wave-deep)"/>
    <path d="M0 290 C250 240 480 280 815 460 L815 481 L0 481Z" fill="var(--wave-light)"/>
    <path d="M0 282 C250 232 480 272 815 452" fill="none" stroke="#fff" stroke-width="12"/>
    <path d="M0 420 C250 370 500 400 815 481 L0 481Z" fill="var(--wave-pale)"/>
  </svg>
  <div class="page-num" style="left:730px">02</div>
</section>

<section class="page page--reason">
  <div class="section-band" style="width:695px"><span class="section-band__title">REASON FOR ATTENDANCE</span></div>

  <p class="intro">Sed ut perspiciatis unde omnis iste natus error sit voluptatem accusantium doloremque laudantium, totam rem aperiaque ab illo inventore veritatis et quasi architecto beatae vitae dicta sunt explicabo.</p>

  <div class="label" style="left:57px;top:283px">Why Attendance Was Required</div>
  <div class="field field--tall" style="left:350px;top:275px;width:408px"></div>
  <div class="label" style="left:57px;top:377px">Call-out type</div>
  <div class="checks" style="left:350px;top:381px;width:420px"><span class="check">Reactive</span><span class="check">Scheduled Maintenance</span><span class="check">Investigation</span><span class="check">Emergency</span></div>
  <div class="label" style="left:57px;top:462px">Reported Issue or Scope<br>Requested by Client</div>
  <div class="field" style="left:350px;top:457px;width:408px"></div>

  <svg class="waves" viewBox="0 0 815 481" height="481" aria-hidden="true">
    <path d="M0 20 C260 0 470 70 815 360 L815 481 L0 481Z" fill="var(--wave-light)"/>
    <path d="M0 55 C270 35 480 110 815 390" fill="none" stroke="#fff" stroke-width="8"/>
    <path d="M0 110 C280 80 500 150 815 420 L815 481 L0 481Z" fill="var(--wave-mid)"/>
    <path d="M0 170 C280 140 500 200 815 440 L815 481 L0 481Z" fill="var(--wave-deep)"/>
    <path d="M0 290 C250 240 480 280 815 460 L815 481 L0 481Z" fill="var(--wave-light)"/>
    <path d="M0 282 C250 232 480 272 815 452" fill="none" stroke="#fff" stroke-width="12"/>
    <path d="M0 420 C250 370 500 400 815 481 L0 481Z" fill="var(--wave-pale)"/>
  </svg>
  <div class="page-num" style="left:717px">03</div>
</section>

</body>
</html>
```